Webdesign für Steuerberaterin
Zielgruppe
Ich bin Steuerberaterin. Meine Zielgruppe sind sowohl Privatpersonen als auch Unternehmer sowie Männer und Frauen.
Aufgabenstellung
Bitte mein Logo und Foto mit berücksichtigen. Ich möchte keine Website, auf der alle 'Reiter' als eine Seite von oben nach unten durchlaufen. Sondern wirklich einzelne, voneinander getrennte Seiten.

```html
<!DOCTYPE html>
<html lang="de">
<head>
<meta charset="utf-8">
<title>Maren Brodtke – Steuerberaterin</title>
<link rel="stylesheet" href="https://fonts.googleapis.com/css2?family=Source+Sans+3:wght@400;600&family=Cormorant+Garamond:wght@500&display=swap">
<style>
  :root {
    --sidebar: #1c1a1f;
    --page: #ffffff;
    --gold: #b08a2e;
    --gold-line: #c9a136;
    --band-top: #dcb83c;
    --band-bottom: #d5ae34;
    --text: #4d4b4f;
    --photo-light: #eeecee;
    --photo-mid: #d9d6d8;
    --photo-dark: #1b1d2e;
  }
  * { margin: 0; padding: 0; box-sizing: border-box; }
  html, body {
    width: 1200px; height: 720px; overflow: hidden;
    background: var(--page);
    font-family: "Source Sans 3", "Myriad Pro", sans-serif;
    color: var(--text);
  }
  .site { position: relative; width: 1200px; height: 720px; }
  .sidebar {
    position: absolute; left: 0; top: 0;
    width: 307px; height: 694px;
    background: var(--sidebar);
  }
  .main-nav { position: absolute; left: 35px; top: 0; }
  .main-nav a {
    position: absolute; left: 0; white-space: nowrap;
    color: var(--gold); text-decoration: none;
    font-size: 14.5px; line-height: 1;
  }
  .brand {
    position: absolute; left: 318px; top: 40px; width: 110px;
    text-align: center;
  }
  .brand-mark {
    width: 14px; height: 14px; border-radius: 50%;
    background: var(--text); margin: 0 auto 8px;
  }
  .brand-name {
    font-family: "Cormorant Garamond", Georgia, serif;
    font-weight: 500; font-size: 19px; color: var(--gold); line-height: 1;
  }
  .brand-role {
    margin-top: 6px; font-size: 6.5px; letter-spacing: 1.6px;
    color: var(--text); text-transform: uppercase;
  }
  .portrait {
    position: absolute; left: 130px; top: 121px;
    width: 478px; height: 350px;
    background:
      radial-gradient(ellipse 28% 60% at 55% 100%, var(--photo-dark) 0 60%, transparent 62%),
      radial-gradient(ellipse 60% 70% at 50% 45%, #fbfafb, var(--photo-light) 55%, var(--photo-mid));
  }
  .welcome {
    position: absolute; left: 627px; top: 0; width: 560px;
    text-align: center;
  }
  .welcome h1 {
    position: absolute; left: 0; right: 0; top: 118px;
    font-family: "Cormorant Garamond", Georgia, serif;
    font-weight: 500; font-size: 25px; color: var(--gold); line-height: 1.2;
  }
  .welcome .rule {
    position: absolute; left: 23px; width: 513px; top: 158px;
    height: 1.5px; background: var(--gold-line);
  }
  .welcome p {
    position: absolute; left: 0; right: 0;
    font-size: 15px; line-height: 20.6px;
  }
  .welcome .lead { top: 181px; font-weight: 600; }
  .welcome .intro { top: 225px; }
  .welcome .invite { top: 351px; }
  .welcome .promise { top: 415px; }
  .footer-band {
    position: absolute; left: 0; top: 694px; width: 1200px; height: 26px;
    background: linear-gradient(var(--band-top), var(--band-bottom));
  }
</style>
</head>
<body>
<div class="site">
  <aside class="sidebar">
    <nav class="main-nav">
      <a href="#" style="top:120px">Über mich</a>
      <a href="#" style="top:165px;left:1px">Leistungen</a>
      <a href="#" style="top:211px">Kontakt</a>
      <a href="#" style="top:257px">Impressum</a>
    </nav>
  </aside>

  <div class="brand">
    <div class="brand-mark"></div>
    <div class="brand-name">Maren Brodtke</div>
    <div class="brand-role">Steuerberaterin</div>
  </div>

  <div class="portrait" role="img" aria-label="Porträtfoto der Steuerberaterin im dunklen Blazer vor heller Steinwand"></div>

  <section class="welcome">
    <h1>Schön, dass Sie da sind</h1>
    <div class="rule"></div>
    <p class="lead">Ich freue mich, dass Sie den Weg zu mir gefunden haben!</p>
    <p class="intro">Sie sind bei mir genau richtig:<br>
      Egal, ob Sie Privatperson sind, die Ihre Einkommensteuer-Erklärung<br>
      in vertrauensvolle Hände geben möchte,<br>
      oder Unternehmer, der sich z.B. das „Rundum-Sorglos-Paket“<br>
      mit Buchführung, Jahresabschluss und Steuererklärungen wünscht.</p>
    <p class="invite">Schauen Sie sich hier gerne um und melden Sie sich bei mir – ich bin bei jedem<br>
      steuerlichen Thema gerne Ihr kompetenter und zuverlässiger Ansprechpartner.</p>
    <p class="promise">Für mich ist es eine Selbstverständlichkeit,<br>
      dass ich auch nach mehr als 12 Jahren Berufserfahrung<br>
      durch permanente Fortbildungen immer auf dem aktuellsten Stand<br>
      der relevanten Gesetze und Verordnungen bin.<br>
      Nur so kann ich Sie bestmöglich beraten.</p>
  </section>

  <div class="footer-band"></div>
</div>
</body>
</html>
```